Tidy paddock Services

After a high quality design website. we are a company that provides services to people that own land and need a hand getting on top of the delayed jobs.
would want a number of tab/ pages for the web page.
Home page / About us page / services page / Gallery page. / Contact us page
we offer a wide range of services .listed below

Stock Work (title)

Stock movement
Break feeding
Temporary staffing

Spraying (title)

Spraying weeds
Spraying gorse

Pastures (title)

Fertilizing
Topping

Building (title)

Habitable sheds
Farm sheds
Sheep yards
Cattle yards
Repair farm buildings
Decks
Retaining walls

Fencing (title)

Stock fencing
Post & rail
Stock yards repair
Electric fencing install & repairs

Water Management (title)

Water trough installation
Water scheme install
Water trough cleaning
Farm water maintenance
Water ponds
Ornamental ponds
Drainage

General (title)

Lawn mowing
Hedge trimming
Pruning trees
Metaling drive ways & races
Water blasting
Small digger work
Little tip truck cartage
Home kill management
Mulching gorse
Section clearing

```html
<!DOCTYPE html>
<html lang="en">
<head>
<meta charset="utf-8">
<title>Tidy paddock Services</title>
<link href="https://fonts.googleapis.com/css2?family=Lato:wght@400;700;900&display=swap" rel="stylesheet">
<style>
:root{
  --green:#6a9a14;
  --green-dark:#557c0e;
  --ink:#161616;
  --body:#3a3a3a;
  --band:#efeeee;
  --white:#ffffff;
}
*{margin:0;padding:0;box-sizing:border-box}
html,body{width:1200px;height:3985px;overflow:hidden}
body{position:relative;font-family:'Lato',sans-serif;color:var(--ink);background:var(--white)}
.abs{position:absolute}
.btn{position:absolute;display:flex;align-items:center;justify-content:center;width:155px;height:37px;border-radius:19px;background:var(--green);color:var(--white);font-weight:700;font-size:15px}
/* hero */
.hero{left:0;top:0;width:1200px;height:728px;background:linear-gradient(180deg,#9c8064 0%,#b87a3c 38%,#6a4022 62%,#2a1a10 100%)}
.hero-curve{left:0;top:0}
.brand{left:62px;top:40px;display:flex;align-items:center;gap:14px;color:var(--white);font-weight:700;font-size:40px;letter-spacing:.5px}
.brand .dot{width:46px;height:46px;border-radius:50%;border:3px solid var(--white);flex:none}
.contact-item{top:38px;display:flex;align-items:center;gap:12px;color:var(--white);font-size:12.5px;line-height:19px}
.contact-item b{display:block;font-weight:700}
.contact-item .ico{width:42px;height:42px;border-radius:50%;background:var(--white);display:flex;align-items:center;justify-content:center}
.nav{top:122px;left:617px;display:flex;gap:44px;color:var(--white);font-size:15px}
.welcome{left:115px;top:296px;color:var(--white);font-size:43px;font-weight:400}
.hero-title{left:113px;top:362px;color:var(--white);font-size:80px;font-weight:900;line-height:92px}
/* features */
.features{left:0;top:728px;width:1200px;height:223px;background:var(--band)}
.feature{top:52px;width:260px;text-align:center;font-size:22px;font-weight:700;line-height:28px}
.feature svg{display:block;margin:0 auto 14px}
/* about */
.about-photo{left:111px;top:1036px;width:360px;height:628px;border-radius:0 360px 360px 0/0 314px 314px 0;background:linear-gradient(160deg,#b7c3a4 0%,#4f7a4a 40%,#3b2f24 100%)}
.about-title{left:580px;top:1094px;font-size:48px;font-weight:700}
.about-text{left:580px;top:1182px;width:515px;font-size:14.5px;line-height:27.5px;color:var(--body)}
.about-text p+p{margin-top:27px}
/* services */
.section-title{width:1200px;left:0;text-align:center;font-size:48px;font-weight:700}
.service{top:1837px;width:300px;text-align:center}
.service .ph{width:300px;height:257px}
.service h3{margin-top:20px;font-size:26px;font-weight:700}
.service p{margin-top:12px;font-size:15.5px;line-height:27px;color:var(--body)}
.service .btn{position:relative;margin:20px auto 0}
.arrow{top:1950px;width:36px;height:36px}
/* gallery */
.gallery{left:0;top:2388px;width:1200px;height:855px;background:linear-gradient(180deg,#efefef 0%,#f3f3f1 60%,#e9ece2 100%)}
.g-img{width:300px;height:257px}
/* footer */
.foot-brand{left:88px;top:3336px;width:270px;display:flex;align-items:center;gap:12px;color:var(--green);font-weight:700;font-size:27px;line-height:31px}
.foot-brand .dot{width:36px;height:36px;border-radius:50%;border:3px solid var(--green);flex:none}
.foot-about{left:113px;top:3458px;width:240px;font-family:'Times New Roman',serif;font-size:12.5px;line-height:25px;color:var(--body)}
.foot-col h4{color:var(--green);font-size:21px;font-weight:700;margin-bottom:12px}
.foot-col li{list-style:none;font-size:14.5px;line-height:38.5px;color:var(--ink)}
.email-field{left:802px;top:3373px;width:274px;height:35px;border-radius:18px;background:var(--ink);color:var(--white);font-size:11.5px;padding:11px 24px}
.social{top:3502px;width:34px;height:34px;border:3px solid var(--green);border-radius:7px}
.copyright{left:0;width:1200px;top:3627px;text-align:center;font-family:'Times New Roman',serif;font-size:12.5px;color:var(--body)}
.pasture{left:0;top:3660px;width:1200px;height:325px;background:linear-gradient(180deg,#ffffff 0%,#cfdcc2 25%,#7fae3e 60%,#5c9a1e 100%)}
</style>
</head>
<body>

<div class="abs hero" role="img" aria-label="Two farmers shaking hands in a field at sunset"></div>
<svg class="abs hero-curve" width="1200" height="728" viewBox="0 0 1200 728" aria-hidden="true">
  <path d="M700 728 C 930 720 1130 650 1200 555 L1200 728 Z" fill="#efeeee"/>
</svg>

<div class="abs brand"><span class="dot"></span>Tidy paddock Services</div>

<div class="abs contact-item" style="left:657px">
  <span class="ico"><svg width="18" height="18" viewBox="0 0 24 24"><path fill="#6a9a14" d="M6.6 10.8a15 15 0 006.6 6.6l2.2-2.2c.3-.3.7-.4 1-.2 1.1.4 2.3.6 3.6.6.6 0 1 .4 1 1V20c0 .6-.4 1-1 1A17 17 0 013 4c0-.6.4-1 1-1h3.5c.6 0 1 .4 1 1 0 1.3.2 2.5.6 3.6.1.3 0 .7-.2 1z"/></svg></span>
  <span><b>Call</b>+1 555 010 0199</span>
</div>
<div class="abs contact-item" style="left:847px">
  <span class="ico"><svg width="18" height="18" viewBox="0 0 24 24"><path fill="#6a9a14" d="M2 5h20v14H2z"/><path d="M2 5l10 8 10-8" fill="none" stroke="#fff" stroke-width="2"/></svg></span>
  <span><b>Email</b>info@tidypaddock.example</span>
</div>

<nav class="abs nav"><span>Home</span><span>About Us</span><span>Services</span><span>Gallery</span><span>Contact Us</span></nav>

<div class="abs welcome">Welcome to</div>
<div class="abs hero-title">TIDY PADDOCK<br>SERVICES</div>
<div class="btn" style="left:113px;top:580px">Contact Us</div>

<section class="abs features">
  <div class="abs feature" style="left:52px">
    <svg width="56" height="56" viewBox="0 0 56 56" fill="none" stroke="#6a9a14" stroke-width="2"><circle cx="30" cy="20" r="11"/><path d="M30 14v12M27 17h5M26 23h6M4 44l12-6h14l10-6 6 4-14 12H12"/></svg>
    Cost Effective
  </div>
  <div class="abs feature" style="left:327px">
    <svg width="56" height="56" viewBox="0 0 56 56" fill="none" stroke="#6a9a14" stroke-width="2"><path d="M6 46a22 22 0 0144 0zM28 46l8-14M18 20l2 4M38 20l-2 4M28 8l2 5h5l-4 3 2 5-5-3-5 3 2-5-4-3h5z"/></svg>
    Performance And<br>Perfection
  </div>
  <div class="abs feature" style="left:617px">
    <svg width="56" height="56" viewBox="0 0 56 56" fill="none" stroke="#6a9a14" stroke-width="2"><circle cx="28" cy="22" r="13"/><path d="M28 13v9l6 4M6 30l6 18h8M50 30l-6 18h-8"/></svg>
    Fast Work Saving<br>Time
  </div>
  <div class="abs feature" style="left:889px">
    <svg width="56" height="56" viewBox="0 0 56 56" fill="none" stroke="#6a9a14" stroke-width="2"><circle cx="28" cy="24" r="6"/><circle cx="14" cy="18" r="5"/><circle cx="42" cy="18" r="5"/><path d="M18 46c0-8 4-12 10-12s10 4 10 12zM4 36c0-6 4-9 10-9M52 36c0-6-4-9-10-9"/></svg>
    Best Workers
  </div>
</section>

<svg class="abs" style="left:830px;top:951px" width="210" height="90" viewBox="0 0 210 90" aria-hidden="true">
  <path d="M9 0a66 66 0 00132 0z" fill="#6a9a14"/>
  <path d="M115 52a42 42 0 0184 0z" fill="#111"/>
</svg>

<div class="abs about-photo" role="img" aria-label="Farm workers hoeing soil between crop rows"></div>
<h2 class="abs about-title">About Us</h2>
<div class="abs about-text">
  <p>Lorem ipsum dolor sit amet, consectetur adipiscing elit, sed do eiusmod tempor incididunt ut labore et dolore magna aliqua. Ut enim ad minim veniam, quis nostrud exercitation ullamco laboris nisi ut aliquip ex ea commodo consequat. Duis aute irure dolor in reprehenderit in voluptate velit esse cillum dolore eu fugiat nulla pariatur.</p>
  <p>Sed ut perspiciatis unde omnis iste natus error sit voluptatem accusantium doloremque laudantium, totam rem aperiam, eaque ipsa quae ab illo inventore veritatis et quasi architecto beatae vitae dicta sunt explicabo. Nemo enim ipsam voluptatem quia voluptas sit aspernatur aut odit aut fugit, sed quia consequuntur magni dolores eos qui ratione voluptatem sequi nesciunt.</p>
</div>
<div class="btn" style="left:581px;top:1557px">Read More</div>

<h2 class="abs section-title" style="top:1742px">Our Services</h2>

<svg class="abs arrow" style="left:53px" viewBox="0 0 36 36" aria-hidden="true"><circle cx="18" cy="18" r="17" fill="#111"/><path d="M26 18H11M17 11l-7 7 7 7" fill="none" stroke="#fff" stroke-width="3.5"/></svg>
<svg class="abs arrow" style="left:1108px" viewBox="0 0 36 36" aria-hidden="true"><circle cx="18" cy="18" r="17" fill="#111"/><path d="M10 18h15M19 11l7 7-7 7" fill="none" stroke="#fff" stroke-width="3.5"/></svg>

<div class="abs service" style="left:111px">
  <div class="ph" role="img" aria-label="Sprayer misting young plants" style="background:linear-gradient(135deg,#d9e6d0,#5e8d3c 55%,#2b4a7a)"></div>
  <h3>Spraying</h3>
  <p>Lorem ipsum dolor sit amet, elit,<br>sed do eiusmod tempor incididunt<br>ut labore et dolore magna aliqua.</p>
  <div class="btn">Read More</div>
</div>
<div class="abs service" style="left:448px">
  <div class="ph" role="img" aria-label="Cattle grazing on green pasture hills" style="background:linear-gradient(180deg,#a9a28c,#7c9a52 45%,#3e3a2c)"></div>
  <h3>Pastures</h3>
  <p>Lorem ipsum dolor sit amet, elit,<br>sed do eiusmod tempor incididunt<br>ut labore et dolore magna aliqua.</p>
  <div class="btn">Read More</div>
</div>
<div class="abs service" style="left:785px">
  <div class="ph" role="img" aria-label="Farmer repairing a wire fence post" style="background:linear-gradient(180deg,#9fb8d6,#6f7a4e 45%,#b5a27a)"></div>
  <h3>Fencing</h3>
  <p>Lorem ipsum dolor sit amet, elit,<br>sed do eiusmod tempor incididunt<br>ut labore et dolore magna aliqua.</p>
  <div class="btn">Read More</div>
</div>

<section class="abs gallery"></section>
<svg class="abs" style="left:830px;top:2338px" width="210" height="52" viewBox="0 0 210 52" aria-hidden="true">
  <path d="M11 50a64 64 0 01128 0z" fill="#6a9a14"/>
  <path d="M115 50a42 42 0 0184 0z" fill="#111"/>
</svg>
<h2 class="abs section-title" style="top:2452px">Gallery</h2>

<div class="abs g-img" style="left:113px;top:2540px;background:linear-gradient(135deg,#d8d6cf,#5a4a3a 50%,#c7b283)" role="img" aria-label="Dairy cows feeding in a barn"></div>
<div class="abs g-img" style="left:450px;top:2540px;background:linear-gradient(180deg,#a6b28a,#3a4f7c 50%,#4a3b30)" role="img" aria-label="Tractor ploughing a field"></div>
<div class="abs g-img" style="left:785px;top:2540px;background:linear-gradient(180deg,#8a5a3a,#c2b8a8 50%,#2a2622)" role="img" aria-label="Farmer walking through a cow barn"></div>
<div class="abs g-img" style="left:113px;top:2835px;background:linear-gradient(180deg,#b9c6d0,#4f7a3c 45%,#8a5a3a)" role="img" aria-label="Farmer hoeing dry soil between crops"></div>
<div class="abs g-img" style="left:450px;top:2835px;background:linear-gradient(160deg,#4e7a2c,#e3e6ea 45%,#2f6a2a)" role="img" aria-label="Worker in protective suit spraying crops"></div>
<div class="abs g-img" style="left:785px;top:2835px;background:linear-gradient(180deg,#6f7c5a,#d8d4c8 50%,#7a6e5e)" role="img" aria-label="Flock of sheep in a yard"></div>

<div class="btn" style="left:523px;top:3131px">View All</div>

<div class="abs foot-brand"><span class="dot"></span><span>Tidy paddock<br>Services</span></div>
<p class="abs foot-about">Lorem ipsum dolor sit amet, consectetur adipiscing elit, sed do eiusmod tempor incididunt ut labore et dolore magna aliqua.</p>

<div class="abs foot-col" style="left:417px;top:3330px">
  <h4>UseFul Links</h4>
  <ul><li>Home</li><li>About Us</li><li>Services</li><li>Gallery</li><li>Contact Us</li></ul>
</div>
<div class="abs foot-col" style="left:597px;top:3330px">
  <h4>Other Links</h4>
  <ul><li>Terms and Conditions</li><li>Help</li><li>Privacy Policy</li><li>Faq</li></ul>
</div>
<div class="abs foot-col" style="left:800px;top:3330px"><h4>Newsletter To Our Subscription</h4></div>
<div class="abs email-field">Email Address:</div>
<div class="btn" style="left:804px;top:3431px;width:128px">Submit</div>
<div class="abs social" style="left:818px"></div>
<div class="abs social" style="left:883px"></div>
<div class="abs social" style="left:948px"></div>

<div class="abs pasture" role="img" aria-label="Cows grazing on a bright green pasture"></div>
<p class="abs copyright">Copyright © 2024 Tidy paddock Services. All rights reserved.</p>

</body>
</html>
```